Design a New Business Card for Our Company

We are looking for fresh, unique, and a modern business card that reflects our roots as digital marketing agency focused on SEM.

Industry/Entity Type

Marketing

Contact Information for Business Card

looking for very unique out of the box designs. clean and modern that compliments our logo

Requirements
Must have
• colors should match our logo
• Front should have name, address, email, and phone/fax of the person, phone/fax are the same number
• back should have our url

```html
<!DOCTYPE html>
<html lang="en">
<head>
<meta charset="utf-8">
<title>Clearpath Media – Business Card</title>
<link href="https://fonts.googleapis.com/css2?family=Roboto:wght@400;500&display=swap" rel="stylesheet">
<style>
  :root {
    --backdrop: #b0aeae;
    --card: #ffffff;
    --band: #9a9a9a;
    --brand-blue: #5b94d0;
    --brand-grey: #a9a9a9;
    --motif-light: #ececec;
    --text-dark: #333333;
    --text-muted: #8f8f8f;
  }
  * { margin: 0; padding: 0; box-sizing: border-box; }
  html, body {
    width: 1200px; height: 1000px; overflow: hidden;
    background: var(--backdrop);
    font-family: "Roboto", Arial, sans-serif;
  }
  .card {
    position: absolute; left: 230px; width: 737px; height: 450px;
    background: var(--card);
    box-shadow: 10px 12px 18px rgba(0,0,0,0.35);
    overflow: hidden;
  }
  /* Back of card */
  .card-back { top: 35px; }
  .motif-field {
    position: absolute; left: 0; width: 100%;
    background: linear-gradient(180deg, #f7f7f7, var(--motif-light) 50%, #f7f7f7);
  }
  .motif-field.top { top: 0; height: 163px; }
  .motif-field.bottom { top: 287px; height: 163px; }
  .brand-band {
    position: absolute; top: 163px; left: 0; width: 100%; height: 124px;
    background: var(--band);
    display: flex; align-items: center; justify-content: center; gap: 16px;
  }
  .brand-band .brand-dot {
    width: 58px; height: 58px; border-radius: 50%; background: #e9e9e9;
  }
  .brand-band .brand-name {
    font-size: 54px; font-weight: 500; color: #eeeeee; letter-spacing: -1px;
  }
  .website {
    position: absolute; top: 398px; left: 0; width: 100%;
    text-align: center; font-size: 22px; font-weight: 500;
    color: var(--brand-blue);
  }

  /* Front of card */
  .card-front { top: 516px; }
  .side-rail { position: absolute; left: 0; top: 0; }
  .holder-name {
    position: absolute; left: 52px; top: 40px;
    font-size: 26px; font-weight: 500; color: var(--brand-blue);
  }
  .holder-title {
    position: absolute; left: 66px; top: 68px;
    font-size: 21px; color: var(--text-muted);
  }
  .contact-list { position: absolute; left: 50px; top: 171px; list-style: none; }
  .contact-list li {
    font-size: 16px; line-height: 19px; color: var(--text-dark);
    margin-bottom: 19px;
  }
  .contact-list li.address { margin-bottom: 8px; }
  .brand-motif {
    position: absolute; right: 0; top: 10px; width: 155px; height: 430px;
    background: radial-gradient(circle at 70% 45%, #dcdcdc, #f4f4f4 60%, #ffffff);
  }
  .front-brand {
    position: absolute; left: 232px; top: 340px;
    display: flex; align-items: center; gap: 14px;
  }
  .front-brand .brand-dot {
    width: 56px; height: 56px; border-radius: 50%; background: var(--brand-blue);
  }
  .front-brand .brand-name {
    font-size: 50px; font-weight: 500; color: var(--brand-grey); letter-spacing: -1px;
  }
</style>
</head>
<body>

<section class="card card-back">
  <div class="motif-field top" role="img" aria-label="Faint repeating brand motif pattern"></div>
  <div class="brand-band">
    <span class="brand-dot"></span>
    <span class="brand-name">Clearpath Media</span>
  </div>
  <div class="motif-field bottom" role="img" aria-label="Faint repeating brand motif pattern"></div>
  <p class="website">www.clearpathmedia.com</p>
</section>

<section class="card card-front">
  <svg class="side-rail" width="60" height="450" viewBox="0 0 60 450">
    <rect x="28" y="0" width="8" height="140" fill="#5b94d0"/>
    <path d="M0 152 L36 138 L36 312 L6 330 L6 450 L0 450 Z" fill="#5b94d0"/>
    <rect x="36" y="0" width="2" height="450" fill="#e6e6e6"/>
    <g fill="none" stroke="#ffffff" stroke-width="2">
      <circle cx="18" cy="189" r="13"/>
      <path d="M18 182 a5 5 0 0 1 5 5 c0 4 -5 9 -5 9 c0 0 -5 -5 -5 -9 a5 5 0 0 1 5 -5 z"/>
      <circle cx="18" cy="227" r="13"/>
      <path d="M13 220 l3 -1 l2 4 l-2 2 c1 2 3 4 5 5 l2 -2 l4 2 l-1 3 c-7 0 -13 -6 -13 -13 z"/>
      <circle cx="18" cy="266" r="13"/>
      <rect x="12" y="262" width="12" height="7"/>
      <rect x="14" y="258" width="8" height="4"/>
      <rect x="14" y="267" width="8" height="5"/>
      <circle cx="18" cy="304" r="13"/>
      <rect x="11" y="299" width="14" height="10"/>
      <path d="M11 299 l7 6 l7 -6"/>
    </g>
  </svg>

  <h1 class="holder-name">Jane Porter</h1>
  <p class="holder-title">President</p>

  <ul class="contact-list">
    <li class="address">1487 Maple Ridge Ave Glendale,<br>CA 91208 USA</li>
    <li>888-555-0142</li>
    <li>888-555-0142</li>
    <li>hello@clearpath.com</li>
  </ul>

  <div class="brand-motif" role="img" aria-label="Large brand motif decoration"></div>

  <div class="front-brand">
    <span class="brand-dot"></span>
    <span class="brand-name">Clearpath Media</span>
  </div>
</section>

</body>
</html>
```